GlassHaven Artbook for Okanagan Region, British Columbia

Creating an art book: GlassHaven, for the Okanagan Wine Region in British Columbia, Canada. Would like smart, modern, clean and linear...cool, sexy urban, not ugly boring suburban... I need a cover that appeals to the wino in all of us! Title: GlassHaven -Marla Dovicki
Updates
Thank you all kindly for your efforts. I have added some files so that you can get a sense of my aesthetic...it's never easy trying to figure it out, is it? I will hopefully have dimensions of book soon...cheers, Marla
would anyone please design a giant wine bottle with the wine label that looks like a label but says glasshaven...just curious to see if it works as a design or not...thank you.
Target Market(s)
Designing this wine art book of quotes to wineries in Okanagan BC. Buyer is wine lover and tourist ready to spend his vacation bucks on this wonderful book!
Look and feel

```html
<!DOCTYPE html>
<html lang="en">
<head>
<meta charset="utf-8">
<title>GlassHaven – Marla Dovicki</title>
<link rel="stylesheet" href="https://fonts.googleapis.com/css2?family=Jost:wght@300;400&display=swap">
<style>
  :root {
    --paper: #ffffff;
    --rose: #ff7373;
    --blush: #ff4d4d;
    --scarlet: #ff3333;
    --crimson: #d60000;
    --claret: #9e0000;
    --title-rose: #ff7070;
    --type-light: #ffffff;
  }
  html, body {
    margin: 0;
    padding: 0;
    overflow: hidden;
    background: var(--paper);
  }
  .cover {
    position: relative;
    width: 1194px;
    height: 1200px;
    overflow: hidden;
    background: var(--paper);
    font-family: "Jost", "Century Gothic", sans-serif;
  }
  .band {
    position: absolute;
    left: 0;
    width: 100%;
  }
  .band--rose    { top: 472px; height: 57px;  background: var(--rose); }
  .band--blush   { top: 529px; height: 89px;  background: var(--blush); }
  .band--scarlet { top: 618px; height: 149px; background: var(--scarlet); }
  .band--crimson { top: 767px; height: 179px; background: var(--crimson); }
  .band--claret  { top: 946px; height: 254px; background: var(--claret); }

  .title {
    position: absolute;
    inset: 0;
    width: 1194px;
    height: 1200px;
  }
  .title text {
    font-family: "Jost", "Century Gothic", sans-serif;
    font-weight: 400;
  }
  .title__first {
    fill: var(--title-rose);
    font-size: 200px;
    letter-spacing: -3px;
  }
  .title__second {
    fill: var(--type-light);
    font-size: 178px;
    letter-spacing: -2px;
  }
  .author {
    position: absolute;
    right: 87px;
    top: 1090px;
    margin: 0;
    color: var(--type-light);
    font-weight: 300;
    font-size: 50px;
    line-height: 1;
    letter-spacing: 1px;
  }
</style>
</head>
<body>
  <main class="cover">
    <div class="band band--rose"></div>
    <div class="band band--blush"></div>
    <div class="band band--scarlet"></div>
    <div class="band band--crimson"></div>
    <div class="band band--claret"></div>

    <svg class="title" viewBox="0 0 1194 1200" role="heading" aria-level="1" aria-label="GlassHaven">
      <text class="title__first" x="160" y="472">GLASS</text>
      <text class="title__second" x="500" y="599">HAVEN</text>
    </svg>

    <p class="author">Marla Dovicki</p>
  </main>
</body>
</html>
```